Meridale Bed Company Needs Business Card

Looking for a very nice looking business card. Creative but not extravagant. We sell beds and pillows across the U.S. and need something professional but catchy. I have attached the logo.

Name : Devin Holt
Title : President
Phone : (800) 471-2960
Email: sleep@quilmora.com
Website: www.quilmora.com

Can be single-sided or double-sided
horizontal or vertical

Can use Blues/Greys

Target Market(s)

Mass Market

Industry/Entity Type

Retail

Contact Information for Business Card

Name : Devin Holt
Title : President
Phone : (800) 471-2960
Email: sleep@quilmora.com
Website: www.quilmora.com

Requirements
Must have
• Clean, Modern, Smooth
• Can use Blues/Greys
• On the other side without the information - have something simple like www.quilmora.com or our logo
Nice to have
• Surprise me
Should not have
• Nothing crazy, nothing cluttered

```html
<!DOCTYPE html>
<html lang="en">
<head>
<meta charset="utf-8">
<title>Quilmora Business Card</title>
<link rel="stylesheet" href="https://fonts.googleapis.com/css2?family=Arimo:wght@400;700&display=swap">
<style>
  :root {
    --backdrop: #2b2b2d;
    --brand-blue: #2ea6df;
    --brand-blue-deep: #1f8fcb;
    --band-grey: #5e5f61;
    --band-grey-dark: #4e4f51;
    --paper: #ffffff;
    --paper-shade: #ececec;
    --ink: #555555;
    --ink-soft: #777777;
    --rule: #c9c9c9;
  }
  * { margin: 0; padding: 0; box-sizing: border-box; }
  html, body {
    width: 1200px; height: 843px; overflow: hidden;
    background: var(--backdrop);
    font-family: "Arimo", Arial, sans-serif;
  }
  .stage {
    width: 1200px; height: 843px;
    display: flex; align-items: center; justify-content: center; gap: 40px;
  }
  .card {
    width: 540px; height: 309px; position: relative; overflow: hidden;
    box-shadow: 0 14px 30px rgba(0,0,0,.45);
  }

  /* Back side */
  .card-back {
    background: linear-gradient(160deg, var(--brand-blue) 0%, var(--brand-blue-deep) 100%);
    display: flex; flex-direction: column; align-items: center; justify-content: center;
  }
  .card-back .wordmark {
    color: var(--paper); font-size: 78px; font-weight: 400; letter-spacing: 2px; line-height: 1;
  }
  .card-back .site {
    color: var(--paper); font-size: 11px; letter-spacing: 5px; margin-top: 22px; opacity: .9;
  }

  /* Front side */
  .card-front { background: linear-gradient(180deg, var(--paper) 60%, var(--paper-shade) 100%); }
  .front-band {
    height: 140px;
    background: linear-gradient(180deg, var(--band-grey) 0%, var(--band-grey-dark) 100%);
    display: flex; align-items: center; justify-content: center;
  }
  .front-band .wordmark {
    color: var(--brand-blue); font-size: 72px; font-weight: 400; letter-spacing: 2px; line-height: 1;
  }
  .front-details {
    height: 169px; display: flex; align-items: center; justify-content: center;
  }
  .identity { text-align: right; padding-right: 22px; }
  .identity .name { color: var(--brand-blue); font-weight: 700; font-size: 20px; }
  .identity .title { color: var(--ink); font-size: 14px; margin-top: 4px; }
  .divider { width: 1px; height: 76px; background: var(--rule); }
  .contacts { list-style: none; padding-left: 18px; }
  .contacts li {
    display: flex; align-items: center; gap: 9px;
    color: var(--ink-soft); font-size: 14px; line-height: 22px;
  }
  .contacts svg { width: 14px; height: 14px; fill: var(--brand-blue); flex: none; }
</style>
</head>
<body>
<main class="stage">
  <section class="card card-back" aria-label="Business card back">
    <div class="wordmark">quilmora</div>
    <div class="site">www.quilmora.com</div>
  </section>

  <section class="card card-front" aria-label="Business card front">
    <div class="front-band">
      <div class="wordmark">quilmora</div>
    </div>
    <div class="front-details">
      <div class="identity">
        <div class="name">Devin Holt</div>
        <div class="title">President</div>
      </div>
      <div class="divider"></div>
      <ul class="contacts">
        <li>
          <svg viewBox="0 0 16 16" aria-hidden="true"><path d="M3 1h3l1.5 4-2 1.3a9 9 0 0 0 4.2 4.2L11 8.5l4 1.5v3a2 2 0 0 1-2 2A13 13 0 0 1 1 3a2 2 0 0 1 2-2z"/></svg>
          (800) 471-2960
        </li>
        <li>
          <svg viewBox="0 0 16 16" aria-hidden="true"><path d="M1 3h14v10H1z M2 4l6 5 6-5" /><path d="M1 3h14L8 8.5z" fill="#ffffff" opacity=".5"/></svg>
          sleep@quilmora.com
        </li>
        <li>
          <svg viewBox="0 0 16 16" aria-hidden="true"><circle cx="8" cy="8" r="7"/><path d="M5 4h3l1 2-2 1 1 3-2 2-1-3-1-1z M10 10l2-1 1 2-2 2z" fill="#ffffff" opacity=".6"/></svg>
          www.quilmora.com
        </li>
      </ul>
    </div>
  </section>
</main>
</body>
</html>
```